Business Card Design for a new Senior Concierge Business 1.3.24

I need a professional business card to handout at networking events for my senior helper business. I would like to use the logo I have uploaded. The design should be clear and easy to read and should list the following information...
Delia Parkhurst
Owner
www.HarborlightElderAides.com
Cedar Hollow, Texas
936.482.5079
Delia@harborlightelderaides.com

Target Market(s)

Senior Citizens

Industry/Entity Type

Personal Helper/ Assisstant

Contact Information for Business Card

I have included the details in the project description box.

Font styles to use
Serif

Colors
0054AA
0677BA
7BADD7
CADEEF
E8F1F8
59FF00
82FF00
B8FF75
E3FFCB
F4FFEA
E54698
E96AAD
F1A4CE
F9D9EA
FCEFF6
6B429C
8869AF
B7A5CE
E3DAEB
F3F0F8

Requirements
Must have
• Include uploaded logo
Nice to have
• The log that has been uploaded
Should not have
• No crazy fonts

```html
<!DOCTYPE html>
<html lang="en">
<head>
<meta charset="utf-8">
<title>Harborlight Elder Aides – Business Card</title>
<link rel="stylesheet" href="https://fonts.googleapis.com/css2?family=Open+Sans:wght@400;600;800&display=swap">
<style>
  :root {
    --stage: #262626;
    --teal: #14909a;
    --teal-light: #2aa5ae;
    --teal-dark: #0f7980;
    --card-dark: #222226;
    --pink: #e0185e;
    --white: #ffffff;
    --heart-tone: #3a2a30;
    --hand-tone: #26302f;
  }
  * { margin: 0; padding: 0; box-sizing: border-box; }
  html, body { width: 1200px; height: 779px; overflow: hidden; background: var(--stage); }
  body { font-family: "Open Sans", Arial, sans-serif; position: relative; }

  .card {
    position: absolute;
    top: 235px;
    width: 540px;
    height: 309px;
    overflow: hidden;
    box-shadow: 0 14px 30px rgba(0,0,0,.55);
  }

  /* Front */
  .card-front { left: 40px; background: var(--teal); }
  .front-pattern {
    position: absolute; inset: 0;
    background:
      radial-gradient(ellipse at 80% 0%, rgba(255,255,255,.28), transparent 55%),
      linear-gradient(160deg, var(--teal-light), var(--teal) 45%, var(--teal-dark));
  }
  .front-brand {
    position: absolute; right: 34px; bottom: 46px;
    display: flex; align-items: center; gap: 8px;
  }
  .brand-dot { width: 14px; height: 14px; border-radius: 50%; background: var(--white); }
  .brand-name { color: var(--white); font-weight: 400; font-size: 19px; letter-spacing: .3px; }

  /* Back */
  .card-back { left: 620px; background: var(--card-dark); border-bottom: 4px solid var(--pink); }
  .back-emblem {
    position: absolute; left: 120px; top: 20px; width: 300px; height: 280px;
    background:
      radial-gradient(ellipse at 50% 40%, var(--heart-tone) 0%, rgba(58,42,48,.5) 45%, transparent 70%),
      radial-gradient(ellipse at 40% 85%, var(--hand-tone) 0%, transparent 55%);
    opacity: .9;
  }
  .back-content {
    position: absolute; inset: 0;
    display: flex; flex-direction: column; align-items: center;
    padding-top: 58px; color: var(--white); text-align: center;
  }
  .person-name { font-weight: 800; font-size: 28px; letter-spacing: .5px; line-height: 1.1; }
  .first-name { color: var(--teal); }
  .last-name { color: var(--pink); }
  .person-role { font-weight: 600; font-size: 14px; margin-top: 4px; }
  .contact-icons { display: flex; gap: 14px; margin: 10px 0 6px; }
  .contact-icons svg { width: 15px; height: 15px; }
  .contact-list { list-style: none; font-size: 14px; line-height: 1.45; }
  .location { font-size: 14px; margin-top: 24px; }
</style>
</head>
<body>

  <section class="card card-front">
    <div class="front-pattern" role="img" aria-label="Repeating pattern of small outlined hearts on teal"></div>
    <div class="front-brand">
      <span class="brand-dot"></span>
      <span class="brand-name">Harborlight Elder Aides</span>
    </div>
  </section>

  <section class="card card-back">
    <div class="back-emblem" role="img" aria-label="Large faint brand emblem in deep red and dark green tones"></div>
    <div class="back-content">
      <h1 class="person-name"><span class="first-name">Delia</span> <span class="last-name">Parkhurst</span></h1>
      <p class="person-role">Owner</p>
      <div class="contact-icons">
        <svg viewBox="0 0 16 16" aria-label="Phone"><path fill="var(--teal)" d="M3.5 1.5l2.5 2.8-1.4 1.6c.9 1.9 2.4 3.4 4.3 4.3l1.6-1.4 2.8 2.5-1.6 2.2C6.8 13.4 2.6 9.2 1.5 3.3z"/></svg>
        <svg viewBox="0 0 16 16" aria-label="Website"><circle cx="8" cy="8" r="6.5" fill="none" stroke="var(--teal)" stroke-width="1.5"/><ellipse cx="8" cy="8" rx="2.8" ry="6.5" fill="none" stroke="var(--teal)" stroke-width="1.2"/><line x1="1.5" y1="8" x2="14.5" y2="8" stroke="var(--teal)" stroke-width="1.2"/></svg>
        <svg viewBox="0 0 16 16" aria-label="Email"><rect x="1.5" y="3.5" width="13" height="9" fill="none" stroke="var(--teal)" stroke-width="1.5"/><path d="M1.5 3.5L8 9l6.5-5.5" fill="none" stroke="var(--teal)" stroke-width="1.5"/></svg>
      </div>
      <ul class="contact-list">
        <li>936.482.5079</li>
        <li>www.HarborlightElderAides.com</li>
        <li>Delia@harborlightelderaides.com</li>
      </ul>
      <p class="location">Cedar Hollow, Texas</p>
    </div>
  </section>

</body>
</html>
```